Maple Gable Business Card

Colors can be blue, grey and white as you see in the attached logo. Needs to have a spot for name, title, phone, email, address, and website. There also needs to be a spot for an agent's picture.

Contact Information for Business Card

See project description.

Colors

Designer to choose colors to be used in the design.

```html
<!DOCTYPE html>
<html lang="en">
<head>
<meta charset="utf-8">
<title>Maple Gable Business Card</title>
<link href="https://fonts.googleapis.com/css2?family=Montserrat:wght@400;500;600;700&display=swap" rel="stylesheet">
<style>
  :root {
    --blue: #2f7bc4;
    --blue-deep: #2a6cab;
    --blue-back: #3a82c9;
    --grey: #3b3b3d;
    --grey-soft: #6a6a6e;
    --white: #ffffff;
    --stage: #ecebe8;
  }
  * { box-sizing: border-box; margin: 0; padding: 0; }
  html, body { width: 1200px; height: 930px; overflow: hidden; }
  body {
    background: var(--stage);
    font-family: "Montserrat", sans-serif;
    position: relative;
  }
  .card {
    position: absolute;
    width: 620px;
    height: 360px;
    border-radius: 26px;
    box-shadow: 0 10px 26px rgba(0,0,0,0.18);
    overflow: hidden;
  }
  .card-back {
    left: 60px; top: 60px;
    background: linear-gradient(135deg, #4a90d4 0%, var(--blue-back) 45%, #2f76bd 100%);
    display: flex; align-items: center; justify-content: center;
  }
  .back-brand { text-align: center; color: var(--blue-deep); }
  .back-name {
    font-weight: 600;
    font-size: 40px;
    letter-spacing: 2px;
    text-transform: uppercase;
    display: flex; align-items: center; gap: 16px;
  }
  .mark-square { width: 26px; height: 26px; background: var(--blue-deep); flex: none; }
  .tagline {
    display: flex; align-items: center; gap: 10px;
    font-weight: 600; text-transform: uppercase;
  }
  .tagline::before, .tagline::after {
    content: ""; flex: 1; height: 2px; background: currentColor;
  }
  .back-brand .tagline { font-size: 16px; letter-spacing: 6px; margin-top: 4px; }

  .card-front {
    left: 520px; top: 490px;
    background: var(--white);
  }
  .front-brand {
    position: absolute; left: 36px; top: 38px;
    width: 230px;
  }
  .front-brand-name {
    color: var(--blue);
    font-weight: 700;
    font-size: 26px;
    letter-spacing: 1px;
    text-transform: uppercase;
    white-space: nowrap;
  }
  .front-brand .tagline {
    color: var(--grey); font-size: 11px; letter-spacing: 4px; margin-top: 2px;
  }
  .agent-photo {
    position: absolute; right: 36px; top: 36px;
    width: 190px; height: 230px;
    border-radius: 14px;
    background: linear-gradient(160deg, #d7e3ef 0%, #a9bfd6 100%);
    border-bottom: 6px solid var(--blue);
  }
  .person { position: absolute; left: 36px; top: 140px; }
  .person-name {
    color: var(--blue); font-weight: 700; font-size: 26px;
    text-transform: uppercase; letter-spacing: 0.5px;
    white-space: nowrap;
  }
  .person-title { color: var(--grey); font-size: 16px; margin-top: 2px; }
  .rule { width: 34px; height: 2px; background: var(--grey); margin: 14px 0 12px; }
  .contacts { list-style: none; }
  .contacts li {
    display: flex; align-items: center; gap: 10px;
    color: var(--grey); font-size: 15px; line-height: 24px;
    white-space: nowrap;
  }
  .contacts svg { width: 14px; height: 14px; flex: none; }
</style>
</head>
<body>
  <section class="card card-back" aria-label="Card back">
    <div class="back-brand">
      <div class="back-name"><span class="mark-square"></span>Maple Gable</div>
      <div class="tagline">Real Estate</div>
    </div>
  </section>

  <section class="card card-front" aria-label="Card front">
    <div class="front-brand">
      <div class="front-brand-name">Maple Gable</div>
      <div class="tagline">Real Estate</div>
    </div>

    <div class="agent-photo" role="img" aria-label="Agent portrait photo"></div>

    <div class="person">
      <div class="person-name">Daniel Whitford</div>
      <div class="person-title">Director</div>
      <div class="rule"></div>
      <ul class="contacts">
        <li>
          <svg viewBox="0 0 24 24"><path fill="#2f7bc4" d="M6.6 10.8a15.1 15.1 0 0 0 6.6 6.6l2.2-2.2c.3-.3.7-.4 1-.2 1.1.4 2.3.6 3.6.6.6 0 1 .4 1 1V20c0 .6-.4 1-1 1A17 17 0 0 1 3 4c0-.6.4-1 1-1h3.5c.6 0 1 .4 1 1 0 1.3.2 2.5.6 3.6.1.3 0 .7-.2 1z"/></svg>
          (555) 218-4473
        </li>
        <li>
          <svg viewBox="0 0 24 24"><rect x="2.5" y="5" width="19" height="14" rx="1.5" fill="none" stroke="#2f7bc4" stroke-width="2"/><path d="M3 6l9 7 9-7" fill="none" stroke="#2f7bc4" stroke-width="2"/></svg>
          info@maplegable.com
        </li>
        <li>
          <svg viewBox="0 0 24 24"><circle cx="12" cy="12" r="9.5" fill="none" stroke="#2f7bc4" stroke-width="2"/><ellipse cx="12" cy="12" rx="4" ry="9.5" fill="none" stroke="#2f7bc4" stroke-width="1.6"/><path d="M2.5 12h19" stroke="#2f7bc4" stroke-width="1.6"/></svg>
          www.maplegable.com
        </li>
        <li>
          <svg viewBox="0 0 24 24"><path fill="#2f7bc4" d="M12 2a7 7 0 0 0-7 7c0 5.2 7 13 7 13s7-7.8 7-13a7 7 0 0 0-7-7zm0 9.5A2.5 2.5 0 1 1 12 6.5a2.5 2.5 0 0 1 0 5z"/></svg>
          214 Linden Avenue, Fairview, OH 43210
        </li>
      </ul>
    </div>
  </section>
</body>
</html>
```